Business Card Design for Flood Rescue 360 - Property Restoration Professionals

I need a business card designed for Flood Rescue 360. We are a full-service property restoration solution. Providing water, fire, smoke & storm restoration as well as mold remediation and full remodel or reconstruction to homes and businesses across Dallas-Fort Worth, TX.
Target Market(s)
home and business owners with insurance covered property damage from water, fire or storm related damage
Industry/Entity Type
property restoration
Contact Information for Business Card
Marcus Pelley General Manager Cell: 214-555-0193 Office: 469-555-0148 email: Marcus@FloodRescue360.example services: Water, Fire, Mold, Reconstruction Tagline: Fast Help When Flood Waters Rise!
Look and feel
Each slider illustrates characteristics of the customer's brand and the style your logo design should communicate.

```html
<!DOCTYPE html>
<html lang="en">
<head>
<meta charset="utf-8">
<title>Flood Rescue 360 – Business Card</title>
<link rel="stylesheet" href="https://fonts.googleapis.com/css2?family=Arimo:wght@400;700&family=Montserrat:wght@400;700&display=swap">
<style>
  :root {
    --backdrop: #d4d7d8;
    --paper: #fbfbfb;
    --brand-blue: #0aa3dc;
    --charcoal: #4a4b4d;
    --ink: #2e2f31;
    --rule: #8a8c8f;
    --white: #ffffff;
  }
  * { box-sizing: border-box; margin: 0; padding: 0; }
  html, body { width: 1200px; height: 829px; overflow: hidden; }
  body {
    background: var(--backdrop);
    font-family: "Arimo", Arial, sans-serif;
    position: relative;
  }
  .card {
    position: absolute;
    top: 266px;
    width: 525px;
    height: 300px;
    box-shadow: 0 14px 30px rgba(0,0,0,0.18);
    overflow: hidden;
  }
  /* Front */
  .card-front { left: 45px; background: var(--paper); }
  .holder { position: absolute; left: 34px; top: 38px; }
  .holder-name {
    color: var(--brand-blue);
    font-weight: 700;
    font-size: 22px;
    letter-spacing: 0.2px;
    text-transform: uppercase;
    white-space: nowrap;
  }
  .holder-title { color: var(--ink); font-size: 14px; margin-top: 2px; }
  .holder-rule {
    position: absolute; left: 34px; top: 98px;
    width: 170px; border-top: 1px solid var(--rule);
  }
  .contact-list { position: absolute; left: 34px; top: 112px; list-style: none; }
  .contact-list li {
    display: flex; align-items: center; gap: 8px;
    color: var(--ink); font-size: 14px; line-height: 22px;
    white-space: nowrap;
  }
  .contact-list svg { width: 11px; height: 11px; fill: var(--brand-blue); flex: none; }
  .brand-front {
    position: absolute; right: 30px; top: 40px;
    display: flex; align-items: center; gap: 10px;
  }
  .brand-name {
    font-family: "Arimo", Arial, sans-serif;
    font-weight: 700;
    font-size: 28px;
    line-height: 0.95;
    text-transform: uppercase;
    text-align: right;
    white-space: nowrap;
  }
  .brand-front .brand-name { color: var(--brand-blue); }
  .brand-dot { width: 36px; height: 36px; border-radius: 50%; flex: none; }
  .brand-front .brand-dot { background: var(--brand-blue); }
  .divider {
    position: absolute; left: 34px; right: 34px; top: 208px;
    border-top: 1px solid var(--rule);
  }
  .website {
    position: absolute; right: 34px; top: 226px;
    display: flex; align-items: center; gap: 8px;
    color: var(--ink); font-size: 14px; white-space: nowrap;
  }
  .website svg { width: 11px; height: 11px; fill: var(--brand-blue); }
  .foot-tab {
    position: absolute; left: 190px; bottom: 0;
    width: 170px; height: 12px; background: var(--brand-blue);
  }
  /* Back */
  .card-back { left: 630px; background: var(--brand-blue); }
  .brand-back {
    position: absolute; left: 0; right: 0; top: 60px;
    display: flex; justify-content: center; align-items: center; gap: 14px;
  }
  .brand-back .brand-name { color: var(--white); font-size: 40px; }
  .brand-back .brand-dot { width: 52px; height: 52px; background: var(--white); }
  .services {
    position: absolute; left: 0; right: 0; top: 168px;
    text-align: center; color: var(--white);
    font-family: "Montserrat", Arial, sans-serif; font-size: 14px; letter-spacing: 1px;
  }
  .tagline-band {
    position: absolute; left: 0; right: 0; top: 212px; height: 34px;
    background: var(--charcoal);
    display: flex; align-items: center; justify-content: center;
  }
  .tagline {
    color: var(--brand-blue);
    font-family: "Montserrat", Arial, sans-serif; font-weight: 700; font-size: 14px;
    letter-spacing: 0.5px; white-space: nowrap;
  }
</style>
</head>
<body>

<section class="card card-front" aria-label="Business card front">
  <div class="holder">
    <h1 class="holder-name">Marcus Pelley</h1>
    <p class="holder-title">General Manager</p>
  </div>
  <div class="holder-rule"></div>
  <ul class="contact-list">
    <li><svg viewBox="0 0 12 12" aria-hidden="true"><path d="M1 4c0-2 2-3 5-3s5 1 5 3l-2 1-1-2H4L3 5zM2 7h8v4H2z"/></svg>469-555-0148</li>
    <li><svg viewBox="0 0 12 12" aria-hidden="true"><path d="M3 0h6v12H3zM4 1v9h4V1z"/></svg>214-555-0193</li>
    <li><svg viewBox="0 0 12 12" aria-hidden="true"><path d="M0 5l6-4 6 4v7H0zM1 5.5l5 3 5-3"/></svg>Marcus@FloodRescue360.example</li>
  </ul>
  <div class="brand-front">
    <p class="brand-name">Flood<br>Rescue 360</p>
    <span class="brand-dot" aria-hidden="true"></span>
  </div>
  <div class="divider"></div>
  <p class="website"><svg viewBox="0 0 12 12" aria-hidden="true"><circle cx="6" cy="6" r="6"/></svg>www.FloodRescue360.example</p>
  <div class="foot-tab"></div>
</section>

<section class="card card-back" aria-label="Business card back">
  <div class="brand-back">
    <p class="brand-name">Flood<br>Rescue 360</p>
    <span class="brand-dot" aria-hidden="true"></span>
  </div>
  <p class="services">Water • Fire • Mold • Reconstruction</p>
  <div class="tagline-band">
    <p class="tagline">Fast Help When Flood Waters Rise!</p>
  </div>
</section>

</body>
</html>
```